Business card design needed

I would like a one sided black business card with the information provided above. Refer to my website www.brightvolleyracquets.com.au for an example of colors I have used for my site, would like to keep this consistent for my business cards also, I will upload my logo below.

I am a new small business that provides tennis customers with racquet re stringing, tennis strings and accessories.

Industry/Entity Type

Small Business

Contact Information for Business Card

Bright Volley Tennis

Owen Whitby
Managing Director

brightvolleyracquets@mailbox.example
www.brightvolleyracquets.com.au
0491 726 305

Racquet Restringing/Tennis Strings/Accessories

Requirements
Must have
• Must have my logo and card must be black

```html
<!DOCTYPE html>
<html lang="en">
<head>
<meta charset="utf-8">
<title>Bright Volley Tennis – Business Card</title>
<link href="https://fonts.googleapis.com/css2?family=PT+Sans:ital,wght@0,400;0,700;1,700&display=swap" rel="stylesheet">
<style>
  :root {
    --backdrop: #e4e2de;
    --card: #0a0a0a;
    --lime: #b5d334;
    --navy: #1f4e80;
    --white: #ffffff;
    --ink: #111111;
  }
  * { box-sizing: border-box; margin: 0; padding: 0; }
  html, body {
    width: 1200px; height: 750px; overflow: hidden;
    background: var(--backdrop);
    font-family: "PT Sans", sans-serif;
  }
  .card {
    position: absolute; left: 75px; top: 75px;
    width: 1050px; height: 597px;
    background: var(--card);
    border-radius: 40px;
    overflow: hidden;
  }
  .brand {
    position: absolute; left: 58px; top: 150px;
    display: flex; align-items: center; gap: 20px;
    color: var(--lime);
    font-weight: 700; font-size: 62px; letter-spacing: 1px;
    line-height: 1;
  }
  .brand-dot {
    width: 42px; height: 42px; border-radius: 50%;
    background: var(--lime); flex: none;
  }
  .name-band {
    position: absolute; left: 613px; top: 298px;
    width: 437px; height: 101px;
    display: flex;
  }
  .name-band .label {
    width: 378px; background: var(--lime); color: var(--ink);
    padding: 13px 0 0 23px;
  }
  .name-band .accent { flex: 1; background: var(--navy); }
  .person-name { font-weight: 700; font-size: 33px; line-height: 1.1; }
  .person-role { font-size: 26px; line-height: 1.3; }
  .services {
    position: absolute; left: 47px; top: 428px;
    list-style: none; color: var(--white);
    font-size: 32px; line-height: 45px;
  }
  .services li { display: flex; align-items: center; gap: 14px; }
  .services li::before {
    content: ""; width: 9px; height: 9px; background: var(--white);
  }
  .contact {
    position: absolute; left: 606px; top: 432px;
    width: 420px;
    list-style: none; color: var(--white);
    font-size: 22px; line-height: 44px;
    white-space: nowrap;
  }
  .contact li { display: flex; align-items: center; gap: 10px; }
  .contact svg { width: 20px; height: 20px; flex: none; }
</style>
</head>
<body>
  <div class="card">
    <div class="brand">
      <span class="brand-dot"></span>
      <span class="brand-name">Bright Volley Tennis</span>
    </div>

    <div class="name-band">
      <div class="label">
        <div class="person-name">Owen Whitby</div>
        <div class="person-role">Managing Director</div>
      </div>
      <div class="accent"></div>
    </div>

    <ul class="services">
      <li>Racquet Restringing</li>
      <li>Tennis Strings</li>
      <li>Accessories</li>
    </ul>

    <ul class="contact">
      <li>
        <svg viewBox="0 0 22 22" aria-hidden="true">
          <path d="M3 9c0-3 4-4 8-4s8 1 8 4v1h-4V8H7v2H3z" fill="var(--lime)"/>
          <path d="M6 11h10l2 6H4z" fill="var(--lime)"/>
          <circle cx="11" cy="14" r="1.8" fill="var(--card)"/>
        </svg>
        0491 726 305
      </li>
      <li>
        <svg viewBox="0 0 22 22" aria-hidden="true">
          <rect x="2" y="5" width="18" height="12" fill="none" stroke="var(--lime)" stroke-width="2"/>
          <path d="M2 5l9 7 9-7" fill="none" stroke="var(--lime)" stroke-width="2"/>
        </svg>
        brightvolleyracquets@mailbox.example
      </li>
      <li>
        <svg viewBox="0 0 22 22" aria-hidden="true">
          <circle cx="11" cy="11" r="9" fill="var(--lime)"/>
          <path d="M2 11h18M11 2v18M5 5c4 3 8 3 12 0M5 17c4-3 8-3 12 0" fill="none" stroke="var(--card)" stroke-width="1.2"/>
        </svg>
        www.brightvolleyracquets.com.au
      </li>
    </ul>
  </div>
</body>
</html>
```